Brenlow Estates Website and Logo Design

We need a new logo and website designed for 'Brenlow Estates Ltd', which is a well established Guernsey property holding company founded in 1934.

The company does not currently have a website. The new website should be similar in style and layout to https://www.quorvanhall.example/.

Target Market(s)

Industry, Media, Tenants

Industry/Entity Type

Property Management

Logo Text

BEL OR Brenlow Estates Ltd OR BE

Coding

Coded - Design and coding required

Number of Pages Required

4 page

Font styles to use
Other font styles liked:
• Helvetica

Requirements
Must have
• The logo laying over the picture (like https://www.quorvanhall.example/).
• Big pictures on homepage (like https://www.quorvanhall.example/)

```html
<!DOCTYPE html>
<html lang="en">
<head>
<meta charset="utf-8">
<title>Brenlow Estates Limited</title>
<link href="https://fonts.googleapis.com/css2?family=Montserrat:wght@400;500;600&family=Roboto:wght@400;500;700&display=swap" rel="stylesheet">
<style>
:root{
  --blue:#2b9be0;
  --ink:#222;
  --text:#555;
  --muted:#888;
  --line:#e2e2e2;
  --footer:#ececec;
  --white:#fff;
}
*{box-sizing:border-box;margin:0;padding:0}
html,body{width:1200px;height:2946px;overflow:hidden}
body{position:relative;background:var(--white);font-family:"Roboto",Arial,sans-serif;color:var(--text)}
.abs{position:absolute}
.center{text-align:center;left:0;width:1200px}
h1,h2,h3{font-family:"Montserrat",Arial,sans-serif;font-weight:400;color:var(--ink)}

/* hero */
.hero{left:0;top:0;width:1200px;height:638px;background:linear-gradient(180deg,#2c4560 0%,#3d5a78 35%,#2e4a66 60%,#1c3552 100%)}
.hero-overlay{left:0;top:0;width:1200px;height:638px;background:rgba(20,40,70,.35)}
.brand{left:75px;top:52px;font-size:27px;font-weight:700;color:var(--blue);font-family:"Roboto",Arial,sans-serif}
.nav{top:58px;right:42px;display:flex;align-items:center;gap:0}
.nav a{color:var(--white);text-decoration:none;font-size:15px;margin-right:44px}
.nav .help{margin-right:0;background:var(--blue);padding:9px 20px;border-radius:3px;font-size:15px}
.hero-title{top:300px;font-family:"Montserrat",Arial,sans-serif;font-weight:600;font-size:40px;color:var(--white)}
.hero-sub{top:358px;font-family:"Montserrat",Arial,sans-serif;font-size:29px;color:var(--white);letter-spacing:.3px}
.dots{display:flex;gap:6px;justify-content:center}
.dots span{width:9px;height:9px;border-radius:50%;background:rgba(255,255,255,.35)}
.dots span.on{background:var(--blue)}

/* intro */
.section-title{font-size:29px;letter-spacing:.5px}
.intro-text{top:784px;left:190px;width:820px;font-size:11.5px;line-height:23px;text-align:center}

/* why */
.why-title{left:100px;top:958px;font-size:30px}
.why-text{left:100px;top:1012px;width:520px;font-size:12.5px;line-height:23.5px}
.btn{left:100px;top:1151px;width:175px;height:49px;background:var(--blue);color:var(--white);font-size:14px;font-weight:500;display:flex;align-items:center;justify-content:center;letter-spacing:.3px}
.why-photo{left:683px;top:937px;width:419px;height:281px;background:linear-gradient(135deg,#1d2a44 0%,#2d3f5e 50%,#18233a 100%)}

/* provide */
.subline{font-size:13px;line-height:29px;color:#444;letter-spacing:.2px}
.service{top:1468px;width:300px;text-align:center}
.service .icon{width:88px;height:88px;border-radius:50%;background:var(--blue);margin:0 auto;display:flex;align-items:center;justify-content:center}
.service h3{margin-top:34px;font-family:"Roboto",Arial,sans-serif;font-weight:500;font-size:16px;letter-spacing:.6px}
.service p{margin-top:14px;font-size:12.5px;line-height:23px;padding:0 30px}
.divider{top:1527px;width:1px;height:160px;background:var(--line)}
.arrow{top:1573px}

/* testimonial */
.testimonial{left:0;top:1807px;width:1200px;height:418px;background:linear-gradient(90deg,#3a3128 0%,#5a4a3a 45%,#4a3d31 70%,#2d2620 100%)}
.testimonial-shade{left:0;top:1807px;width:1200px;height:418px;background:rgba(0,0,0,.25)}
.quote-text{top:1992px;left:230px;width:740px;text-align:center;color:var(--white);font-size:18px;line-height:32px}
.quote-name{top:2082px;color:var(--blue);font-size:22px}

/* partners */
.partner{top:2478px;height:42px;background:#d8d8d8;border-radius:4px}

/* footer */
.footer{left:0;top:2612px;width:1200px;height:269px;background:var(--footer)}
.f-head{font-size:13px;font-weight:500;color:var(--ink);letter-spacing:.3px}
.f-text{font-size:11.5px;line-height:24.5px;color:#666}
.f-list{list-style:none;font-size:11.5px;line-height:28px;color:#666}
.f-link{color:var(--blue);font-size:11.5px;font-weight:500}
.social{display:flex;gap:9px}
.social span{width:27px;height:27px;border-radius:50%;background:var(--blue)}
.copyright{top:2906px;font-size:11px;color:#777}
</style>
</head>
<body>

<!-- Hero -->
<div class="abs hero" role="img" aria-label="Harbour with moored boats and a hillside town behind"></div>
<div class="abs hero-overlay"></div>
<div class="abs brand">Brenlow Estates <span style="color:var(--white);font-weight:700">Limited</span></div>
<nav class="abs nav">
  <a href="#">About Us</a><a href="#">Services</a><a href="#">Blog</a><a href="#">Testimonials</a><a href="#">Contact Us</a><a href="#" class="help">Need Help?</a>
</nav>
<h1 class="abs center hero-title">BRENLOW ESTATES LIMITED</h1>
<div class="abs center hero-sub">IS A FAMILY-OWNED GUERNSEY PROPERTY HOLDING COMPANY</div>
<div class="abs center dots" style="top:604px"><span class="on"></span><span></span><span></span></div>

<!-- Intro -->
<h2 class="abs center section-title" style="top:718px">BRENLOW ESTATES LIMITED</h2>
<p class="abs intro-text">Brenlow Estates Limited (BEL) is a family-owned Guernsey property holding company. It purchases properties that are considered to have potential for development either through refurbishment or by obtaining planning permission to change its classification from, for example, industrial premises to offices or retail outlets, or by the marriage value of buying an adjacent property to one already owned by BEL.</p>

<!-- Why Guernsey -->
<h2 class="abs why-title">WHY GUERNSEY?</h2>
<p class="abs why-text">The Bailiwick of Guernsey is a British Crown dependency in the English Channel. The benefit of establishing a company in Guernsey is the island's low tax jurisdiction since there are no capital taxes and no corporation taxes for many companies. Consequently since the 1980s the island's development as an ideal financial centre for the establishment of institutions and banks has thrived.</p>
<div class="abs btn">READ MORE INFO</div>
<div class="abs why-photo" role="img" aria-label="Businessman in a dark suit holding a small house symbol in cupped hands"></div>

<!-- We Provide -->
<h2 class="abs center section-title" style="top:1308px">WE PROVIDE</h2>
<p class="abs center subline" style="top:1364px">INDUSTRIAL PREMISES TO OFFICES OR RETAIL OUTLETS, OR BY THE MARRIAGE VALUE OF BUYING AN ADJACENT PROPERTY<br>TO ONE ALREADY OWNED BY BEL.</p>

<svg class="abs arrow" style="left:74px" width="16" height="44" viewBox="0 0 16 44"><path d="M14 2 L2 22 L14 42" fill="none" stroke="#ccc" stroke-width="2"/></svg>
<svg class="abs arrow" style="left:1108px" width="16" height="44" viewBox="0 0 16 44"><path d="M2 2 L14 22 L2 42" fill="none" stroke="#ccc" stroke-width="2"/></svg>

<div class="abs service" style="left:101px">
  <div class="icon"><svg width="46" height="46" viewBox="0 0 46 46" fill="none" stroke="#fff" stroke-width="2"><path d="M5 22 L23 7 L41 22"/><path d="M10 18 V40 H36 V18"/><rect x="19" y="27" width="8" height="13"/><path d="M31 6 L39 6 L39 14"/></svg></div>
  <h3>DEALING PROPERTY</h3>
  <p>Lorem Ipsum es simplemente el texto de relleno de las imprentas y archivos de texto. Lorem Ipsum ha sido el texto de relleno estándar de las industrias</p>
</div>
<div class="abs divider" style="left:424px"></div>
<div class="abs service" style="left:449px">
  <div class="icon"><svg width="46" height="46" viewBox="0 0 46 46" fill="none" stroke="#fff" stroke-width="2"><path d="M5 22 L23 7 L41 22"/><path d="M10 18 V40 H36 V18"/><circle cx="28" cy="31" r="6"/><path d="M25 31 L27.5 33.5 L31 29"/></svg></div>
  <h3>AVAILABLE PROPERTIES</h3>
  <p>Lorem Ipsum es simplemente el texto de relleno de las imprentas y archivos de texto. Lorem Ipsum ha sido el texto de relleno estándar de las industrias</p>
</div>
<div class="abs divider" style="left:772px"></div>
<div class="abs service" style="left:797px">
  <div class="icon"><svg width="46" height="46" viewBox="0 0 46 46" fill="none" stroke="#fff" stroke-width="2"><rect x="6" y="8" width="34" height="24"/><path d="M11 26 L18 19 L24 23 L34 13"/><path d="M23 32 V38 M16 40 L23 32 L30 40"/></svg></div>
  <h3>ANNUAL PROPERTY</h3>
  <p>Lorem Ipsum es simplemente el texto de relleno de las imprentas y archivos de texto. Lorem Ipsum ha sido el texto de relleno estándar de las industrias</p>
</div>

<!-- Testimonial -->
<div class="abs testimonial" role="img" aria-label="Man with glasses working thoughtfully at a laptop in a warm-toned office"></div>
<div class="abs testimonial-shade"></div>
<svg class="abs" style="left:574px;top:1918px" width="52" height="42" viewBox="0 0 52 42" fill="var(--blue)"><path d="M2 2 H22 V22 Q22 36 8 40 L6 34 Q14 31 14 24 H2 Z"/><path d="M30 2 H50 V22 Q50 36 36 40 L34 34 Q42 31 42 24 H30 Z"/></svg>
<p class="abs quote-text">Lorem Ipsum es simplemente el texto de relleno de las imprentas y archivos de texto. Lorem Ipsum ha sido el texto de relleno estándar de las industrias</p>
<div class="abs center quote-name">- Marcus Hollen -</div>
<div class="abs center dots" style="top:2170px"><span class="on"></span><span></span><span></span></div>

<!-- Partners -->
<h2 class="abs center section-title" style="top:2309px">OUR PARTNERS</h2>
<p class="abs center subline" style="top:2369px">INDUSTRIAL PREMISES TO OFFICES OR RETAIL OUTLETS, OR BY THE MARRIAGE VALUE OF BUYING AN ADJACENT PROPERTY<br>TO ONE ALREADY OWNED BY BEL.</p>
<div class="abs partner" style="left:141px;width:134px"></div>
<div class="abs partner" style="left:326px;width:134px"></div>
<div class="abs partner" style="left:510px;width:128px"></div>
<div class="abs partner" style="left:688px;width:134px"></div>
<div class="abs partner" style="left:874px;width:178px"></div>

<!-- Footer -->
<footer class="abs footer"></footer>
<div class="abs" style="left:104px;top:2655px;width:360px">
  <div class="f-head">WHO WE ARE?</div>
  <p class="f-text" style="margin-top:14px">Brenlow Estates Limited (BEL) is a family-owned Guernsey property holding company. It purchases properties that are considered to have potential for development either through refurbishment or by obtaining planning permission...</p>
  <div class="f-link" style="margin-top:12px">Read more info &#x25B8;</div>
</div>
<div class="abs" style="left:532px;top:2655px">
  <div class="f-head">WELCOME</div>
  <ul class="f-list" style="margin-top:10px"><li>Home</li><li>About Us</li><li>Services</li><li>Blog</li><li>Testimonials</li><li>Contact Us</li></ul>
</div>
<div class="abs" style="left:711px;top:2655px">
  <div class="f-head">INFORMATION</div>
  <ul class="f-list" style="margin-top:10px"><li>Terms &amp; Conditions</li><li>Privacy policy</li><li>Disclaimer</li><li>Sitemap</li></ul>
</div>
<div class="abs" style="left:900px;top:2655px;width:260px">
  <div class="f-head">CONTACT INFO</div>
  <p class="f-text" style="margin-top:12px">120 Street name, City name,<br>Country name : 3652235</p>
  <p class="f-text" style="margin-top:4px;display:flex;align-items:center;gap:10px"><svg width="12" height="12" viewBox="0 0 12 12"><path d="M2 1 L5 1 L6 4 L4.5 5 Q5.5 7 7 7.5 L8 6 L11 7 L11 10 Q6 11 2.5 7.5 Q0.5 4.5 2 1 Z" fill="var(--blue)"/></svg>( 0148 ) 720 415</p>
  <p class="f-text" style="margin-top:4px;display:flex;align-items:center;gap:10px"><svg width="12" height="10" viewBox="0 0 12 10"><rect x="0" y="0" width="12" height="10" fill="var(--blue)"/><path d="M0 0 L6 5 L12 0" fill="none" stroke="#fff" stroke-width="1"/></svg>info@brenlowestates.example</p>
  <div class="social" style="margin-top:12px"><span></span><span></span><span></span><span></span><span></span></div>
</div>
<div class="abs center copyright">© 2016. Brenlow Estates Limited. All rights reserved</div>

</body>
</html>
```